Website Design for recruiting company

We need a homepage mockup for a recruiting company focused on the legal industry. Use your creative talent to come up with something visually appeal and professional for this web-site.

We'd really like to see the maze from the logo incorporated into the design somehow. Please use the website mockup provided as inspiration for this project. We really like the layout and photos!

Target Market(s)

lawyers

Industry/Entity Type

Legal

Number of Pages Required

1 page

Font styles to use
Sans Serif

```html
<!DOCTYPE html>
<html lang="en">
<head>
<meta charset="utf-8">
<title>Harborline Legal Search</title>
<link href="https://fonts.googleapis.com/css2?family=Montserrat:wght@500;600;700&family=Open+Sans:wght@300;400;600&display=swap" rel="stylesheet">
<style>
:root{
  --plum:#736470;
  --plum-dark:#6a5b67;
  --ink:#1c1c1c;
  --text:#555;
  --muted:#7b6f79;
  --soft:#f2f2f2;
  --white:#fff;
  --ring:#e6e6e6;
}
*{box-sizing:border-box;margin:0;padding:0}
html,body{width:1200px;height:3921px;overflow:hidden}
body{position:relative;font-family:"Open Sans",sans-serif;color:var(--text);background:var(--white)}
.abs{position:absolute}

/* hero */
.hero{position:absolute;left:0;top:0;width:1200px;height:632px;
  background:radial-gradient(circle at 50% 45%,#4c5a3a 0,#3d4a2f 30%,#55633a 55%,#2f3a26 100%)}
.brand{position:absolute;left:19px;top:19px;display:flex;align-items:center;gap:14px}
.brand-mark{width:96px;height:96px;border-radius:50%;border:3px solid var(--white)}
.brand-name{font-family:"Open Sans",sans-serif;font-weight:400;font-size:15px;color:var(--white)}
.nav{position:absolute;top:58px;left:0;width:100%;font-family:"Open Sans",sans-serif;font-weight:600;font-size:14px;color:var(--white)}
.nav span{position:absolute;transform:translateX(-50%);white-space:nowrap}
.nav svg{position:absolute;left:936px;top:2px}
.btn-outline{position:absolute;left:1004px;top:47px;width:175px;height:46px;border:1.5px solid var(--white);border-radius:23px;
  color:var(--white);font-family:"Open Sans",sans-serif;font-weight:600;font-size:15px;display:flex;align-items:center;justify-content:center}
.hero-title{position:absolute;top:245px;left:0;width:100%;text-align:center;color:var(--white);font-family:"Montserrat",sans-serif;font-weight:500;font-size:48px;line-height:62px}
.hero-title strong{font-weight:700;font-size:62px}
.scroll-down{position:absolute;left:572px;top:551px;width:56px;height:56px;border:1.5px solid var(--white);border-radius:50%;display:flex;align-items:center;justify-content:center}

/* about */
.about-photo{position:absolute;left:121px;top:723px;width:412px;height:412px;border-radius:50%;
  background:linear-gradient(135deg,#c9cdd3 0%,#aab4c0 45%,#34465c 75%,#d9c9a8 100%)}
.dot{position:absolute;border-radius:50%;background:var(--ring)}
.about-text{position:absolute;left:600px;top:790px;width:478px}
.section-title{font-family:"Montserrat",sans-serif;font-weight:700;font-size:36px;color:var(--ink);letter-spacing:.3px}
.about-text p{margin-top:28px;font-size:16px;line-height:34px;text-align:justify;color:#555}

/* what's new */
.news{position:absolute;left:0;top:1224px;width:1200px;height:1898px;background:var(--soft)}
.news .section-title{position:absolute;top:80px;width:100%;text-align:center}
.btn-pill{position:absolute;border-radius:25px;display:flex;align-items:center;justify-content:center;font-family:"Open Sans",sans-serif;font-weight:600;font-size:16px}
.btn-plum{background:var(--plum);color:var(--white)}
.btn-white{background:var(--white);color:var(--plum)}
.job{position:absolute;left:90px;width:1020px;height:301px;background:var(--white);display:flex}
.job.flip{flex-direction:row-reverse}
.job-tag{width:257px;flex:none;background:var(--plum);color:var(--white);padding:16px 14px}
.job-tag h3{font-family:"Montserrat",sans-serif;font-weight:600;font-size:27px;line-height:38px;text-transform:uppercase}
.meta{margin-top:18px;font-size:16px;line-height:34px}
.meta div{display:flex;align-items:center;gap:14px}
.meta svg{flex:none}
.meta b{font-weight:600}
.job-body{flex:1;padding:26px 24px 0 22px;font-size:15.5px;line-height:30.5px;text-align:justify}
.job.flip .job-body{padding:26px 76px 0 27px}
.job-body a{display:inline-block;margin-top:6px;color:#555;font-weight:600;text-decoration:underline}

/* employers */
.employers{position:absolute;left:0;top:3122px;width:1200px;height:312px;background:var(--plum);color:var(--white);text-align:center}
.employers .section-title{color:var(--white);position:absolute;top:56px;width:100%}
.employers p{position:absolute;top:110px;width:100%;font-size:18px;line-height:30px}

/* footer */
.footer-brand{position:absolute;left:92px;top:3525px;display:flex;align-items:center;gap:12px}
.footer-brand .brand-mark{border-color:#b5adb3;width:92px;height:92px}
.footer-brand .brand-name{color:var(--muted);font-size:14px}
.footer-rule{position:absolute;left:372px;top:3571px;width:738px;height:1px;background:#ddd}
.fcol{position:absolute;top:3634px;color:var(--muted)}
.fcol h4{font-family:"Open Sans",sans-serif;font-weight:600;font-size:18px;margin-bottom:14px}
.fcol p,.fcol li{font-size:15px;line-height:30px;list-style:none}
.contact li{display:flex;gap:18px}
.contact svg{flex:none;margin-top:9px}
.social{display:flex;gap:18px;margin-top:10px}
.social span{width:11px;height:11px;border-radius:50%;background:var(--muted)}
.bottom-rule{position:absolute;left:90px;top:3868px;width:1020px;height:1px;background:#ddd}
.copyright{position:absolute;top:3889px;width:100%;text-align:center;font-size:12px;color:#888}
</style>
</head>
<body>

<header class="hero" role="img" aria-label="Aerial photograph of a circular hedge maze in a green park">
  <div class="brand"><div class="brand-mark"></div><span class="brand-name">harborline legal search</span></div>
  <nav class="nav">
    <span style="left:390px">About Us</span>
    <span style="left:503px">What's New</span>
    <span style="left:634px">For Employers</span>
    <span style="left:754px">Regional</span>
    <span style="left:861px">Contact Us</span>
    <svg width="15" height="15" viewBox="0 0 15 15" aria-label="Search"><circle cx="6" cy="6" r="4.5" fill="none" stroke="#fff" stroke-width="2"/><path d="M9.5 9.5l4 4" stroke="#fff" stroke-width="2.2" stroke-linecap="round"/></svg>
  </nav>
  <div class="btn-outline">Submit Resume</div>
  <h1 class="hero-title"><strong>Start Here,</strong> Let Our<br>Experience Guide You</h1>
  <div class="scroll-down"><svg width="16" height="10" viewBox="0 0 16 10"><path d="M2 2l6 6 6-6" fill="none" stroke="#fff" stroke-width="2"/></svg></div>
</header>

<section class="about">
  <div class="dot" style="left:212px;top:709px;width:72px;height:72px"></div>
  <div class="dot" style="left:74px;top:1016px;width:118px;height:118px"></div>
  <div class="dot" style="left:472px;top:968px;width:112px;height:112px"></div>
  <div class="about-photo" role="img" aria-label="Smiling lawyer seated at a desk in a bright office"></div>
  <div class="about-text">
    <h2 class="section-title">ABOUT US</h2>
    <p>Harborline Legal Search focuses on the permanent placement of attorneys with law firms and corporations in the New England area. Founded in 1982, Harborline Legal Search is the oldest attorney search firm in New England, and is ranked the number one legal recruiter in New England in the most recent survey conducted by <em>The Counsel Review.</em></p>
  </div>
</section>

<section class="news">
  <h2 class="section-title">WHAT’S NEW</h2>
  <div class="btn-pill btn-plum" style="left:527px;top:143px;width:146px;height:49px">Search Jobs</div>
</section>

<svg width="0" height="0" style="position:absolute">
  <defs>
    <symbol id="i-user" viewBox="0 0 12 13"><circle cx="6" cy="3.5" r="3.2" fill="currentColor"/><path d="M0 13c0-4 2.5-5.5 6-5.5S12 9 12 13z" fill="currentColor"/></symbol>
    <symbol id="i-cal" viewBox="0 0 13 13"><rect x="0.5" y="2" width="12" height="10.5" fill="none" stroke="currentColor"/><rect x="0.5" y="2" width="12" height="3" fill="currentColor"/><path d="M3 0v3M10 0v3" stroke="currentColor" stroke-width="1.5"/><path d="M3 7h1.5M6 7h1.5M9 7h1.5M3 9.5h1.5M6 9.5h1.5M9 9.5h1.5" stroke="currentColor"/></symbol>
  </defs>
</svg>

<article class="job" style="top:1447px">
  <div class="job-tag"><h3>In-House/<br>Corporate/<br>M&amp;A</h3>
    <div class="meta"><div><svg width="12" height="13" style="color:#fff"><use href="#i-user"/></svg><b>Job Id : 2772</b></div><div><svg width="13" height="13" style="color:#fff"><use href="#i-cal"/></svg>Listing Date: 02/10/2020</div></div></div>
  <div class="job-body">Global exchange-listed medical technology leader seeks 8+ year M&amp;A specialist with major law firm training for lead role on all M&amp;A and other BD transactions. As a key member of the leadership team, this role will partner with the Vice President, Corporate Business Development to lead M&amp;A transactions from inception to closing and working effectively with Business Development, Corporate and Divisional Finance and Divisional Legal teams. Will be primarily dedicated to M&amp;A activity with responsibility for the negotiation, execution and all requisite legal support for strategic initiatives such as mergers and acquisitions, divestitures, licenses, alliances and collaborations, joint ventures and other.<br><a>Read More</a></div>
</article>

<article class="job flip" style="top:1768px">
  <div class="job-tag"><h3>Associate/<br>Litigation</h3>
    <div class="meta"><div><svg width="12" height="13" style="color:#fff"><use href="#i-user"/></svg><b>Job Id: 2778</b></div><div><svg width="13" height="13" style="color:#fff"><use href="#i-cal"/></svg>Listing Date: 02/04/2020</div></div></div>
  <div class="job-body">Highly regarded mid-size national firm seeks litigation associate with 4-8 years of experience to join their Litigation Practice. This associate will work on a wide array of litigation matters including, construction, real estate, employment, shareholder and general business disputes. Fantastic opportunity to deal directly with clients and gain hands-on experience. Excellent work-life balance. Law firm experience preferred.</div>
</article>

<article class="job" style="top:2088px">
  <div class="job-tag"><h3>In-House/<br>Senior<br>Corporate<br>Counsel/<br>Securities</h3>
    <div class="meta" style="margin-top:10px"><div><svg width="12" height="13" style="color:#fff"><use href="#i-user"/></svg><b>Job Id: 2768</b></div><div><svg width="13" height="13" style="color:#fff"><use href="#i-cal"/></svg>Listing Date: 01/29/2020</div></div></div>
  <div class="job-body">Leading Cambridge-based exchange-listed biotechnology company seeks 10+ year industry-experienced corporate/securities attorney for lead role in all public company matters and ongoing compliance, corporate governance, and corporate financing transactions. He/she will work closely with the executive team, business leadership, the legal, investor relations, human resources, finance, and business development departments, and outside counsel to further the Company’s ambitious agenda. This position offers exposure and involvement in a wide range of practice areas relevant to a high-growth, fast moving newly public platform-based biotechnology company.<br><a>Read More</a></div>
</article>

<article class="job flip" style="top:2409px">
  <div class="job-tag"><h3>In-House/<br>Biotech/<br>Contracts</h3>
    <div class="meta"><div><svg width="12" height="13" style="color:#fff"><use href="#i-user"/></svg><b>Job Id: 2777</b></div><div><svg width="13" height="13" style="color:#fff"><use href="#i-cal"/></svg>Listing Date: 01/28/2020</div></div></div>
  <div class="job-body" style="text-align:left">Outstanding opportunity for 3+ year attorney to join a premier biotech company in contracts counsel role. Prior experience drafting and negotiating biotech agreements including Clinical Trial Agreements, Master Service Agreements and related research and development contracts is required. Terrific opportunity to join highly collegial team with great work/life balance. Strong compensation.</div>
</article>

<article class="job" style="top:2731px">
  <div class="job-tag"><h3>In-House /<br>Life Sciences /<br>Securities</h3>
    <div class="meta"><div><svg width="12" height="13" style="color:#fff"><use href="#i-user"/></svg><b>Job Id: 2773</b></div><div><svg width="13" height="13" style="color:#fff"><use href="#i-cal"/></svg>Listing Date: 01/14/2020</div></div></div>
  <div class="job-body" style="text-align:left;padding-right:120px">Terrific opportunity for 3rd – 6th year corporate attorney to join outstanding MA-based exchange-listed biopharmaceutical company. Major firm and strong securities and corporate governance experience required, including demonstrated knowledge of U.S. securities law and experience coordinating filings and disclosures. M&amp;A and/or licensing experience a plus. Stellar legal team and strong compensation.</div>
</article>

<section class="employers">
  <h2 class="section-title">FOR EMPLOYERS</h2>
  <p>Our unparalleled recruiting industry and legal experience have generated an<br>extensive network of contacts throughout the legal community.</p>
  <div class="btn-pill btn-white" style="left:527px;top:200px;width:146px;height:48px">Start Here</div>
</section>

<footer>
  <div class="footer-brand"><div class="brand-mark"></div><span class="brand-name">harborline legal search</span></div>
  <div class="footer-rule"></div>
  <div class="fcol" style="left:90px;width:380px;top:3633px">
    <p>Lorem ipsum dolor sit amet, consectetur adipiscing elit, sed do eiusmod tempor incididunt ut labore et dolore magna aliqua.</p>
    <h4 style="margin-top:38px;margin-bottom:6px">Follow Us</h4>
    <div class="social"><span></span><span></span><span></span><span></span><span></span></div>
  </div>
  <div class="fcol" style="left:583px">
    <h4>Links</h4>
    <ul><li>About Us</li><li>What's New</li><li>For Employers</li><li>Regional</li><li>Contact Us</li></ul>
  </div>
  <div class="fcol contact" style="left:828px;width:290px">
    <h4>Contact Us</h4>
    <ul>
      <li><svg width="10" height="13" viewBox="0 0 10 13"><path d="M5 0a5 5 0 0 0-5 5c0 3.5 5 8 5 8s5-4.5 5-8a5 5 0 0 0-5-5z" fill="#7b6f79"/><circle cx="5" cy="5" r="1.8" fill="#fff"/></svg><span>Harborline Legal Search, P.O. Box 40418, Portside MA 02990</span></li>
      <li><svg width="12" height="12" viewBox="0 0 12 12"><path d="M2.5 0l2 3-1.3 1.5a7 7 0 0 0 4.3 4.3L9 7.5l3 2-1 2.5C5 12 0 7 0 1z" fill="#7b6f79"/></svg><span>Tel: 555.014.2290</span></li>
      <li><svg width="13" height="12" viewBox="0 0 13 12"><rect x="3" y="0" width="7" height="4" fill="#7b6f79"/><rect x="0" y="4" width="13" height="6" rx="1" fill="#7b6f79"/><rect x="3" y="8" width="7" height="4" fill="#fff" stroke="#7b6f79"/></svg><span>Fax: 555.014.2291</span></li>
      <li><svg width="13" height="10" viewBox="0 0 13 10"><rect width="13" height="10" fill="#7b6f79"/><path d="M0 0l6.5 5L13 0" fill="none" stroke="#fff"/></svg><span>hello@harborlinesearch.example</span></li>
    </ul>
  </div>
  <div class="bottom-rule"></div>
  <div class="copyright">© 2020 The Company Name. All rights Reserved.</div>
</footer>

</body>
</html>
```